Stonebridge Building and Projects business cards

A business card with watermark background (construction work)

Company logo attached

Home improvement projects
House renovations
Bathroom and kitchen renovations
House extensions
New builds and granny flats

Director Omar Haddani
(Phone number)
omar@sbpbuilding.com.au
(Instagram logo) sbp_building

```html
<!DOCTYPE html>
<html lang="en">
<head>
<meta charset="utf-8">
<title>Stonebridge Building and Projects – Business Cards</title>
<link rel="stylesheet" href="https://fonts.googleapis.com/css2?family=Poppins:wght@400;500;600&family=Roboto:wght@400&display=swap">
<style>
  :root {
    --backdrop: #8b6c4c;
    --card: #f7f7f7;
    --brand-blue: #2b73b9;
    --ink: #1e1e1e;
    --rule: #2b73b9;
  }
  * { box-sizing: border-box; margin: 0; padding: 0; }
  html, body { width: 900px; height: 1200px; overflow: hidden; }
  body { background: var(--backdrop); position: relative; font-family: "Roboto", sans-serif; color: var(--ink); }

  .card {
    position: absolute;
    background: var(--card);
    border-radius: 24px;
    box-shadow: 0 6px 18px rgba(0,0,0,0.25);
  }
  .card--front { left: 72px; top: 135px; width: 773px; height: 448px; }
  .card--back  { left: 74px; top: 625px; width: 773px; height: 447px; }

  .wordmark {
    position: absolute;
    font-family: "Poppins", sans-serif;
    font-weight: 600;
    color: var(--brand-blue);
    text-align: center;
    line-height: 1.15;
  }
  .card--front .wordmark { left: 40px; top: 230px; width: 330px; font-size: 30px; transform: translateY(-50%); }
  .card--back .wordmark  { left: 193px; top: 180px; width: 400px; font-size: 38px; transform: translateY(-50%); }
  .wordmark__sub { display: block; }

  .contact-name {
    position: absolute; left: 400px; top: 86px;
    font-family: "Poppins", sans-serif; font-weight: 600;
    font-size: 31px; color: var(--brand-blue); line-height: 1;
  }
  .contact-role {
    position: absolute; left: 400px; top: 124px;
    font-family: "Poppins", sans-serif; font-weight: 400;
    font-size: 22px; line-height: 1;
  }
  .contact-list { position: absolute; left: 402px; top: 193px; list-style: none; }
  .contact-list li {
    display: flex; align-items: center; gap: 10px;
    font-size: 20px; height: 39px;
  }
  .contact-list svg { width: 24px; height: 22px; flex: none; }

  .service-rule { position: absolute; height: 2px; background: var(--rule); }
  .card--front .service-rule { left: 35px; width: 705px; top: 372px; }
  .card--back .service-rule  { left: 43px; width: 701px; top: 370px; }

  .services {
    position: absolute; left: 0; width: 100%;
    text-align: center; font-size: 20px; white-space: nowrap;
  }
  .card--front .services { top: 388px; }
  .card--back .services  { top: 388px; }
  .services .sep { margin: 0 10px; }
</style>
</head>
<body>

<section class="card card--front" aria-label="Business card front">
  <div class="wordmark">
    <span class="wordmark__sub">Stonebridge</span>
    <span class="wordmark__sub">Building and Projects</span>
  </div>

  <h1 class="contact-name">Omar Haddani</h1>
  <p class="contact-role">Director</p>

  <ul class="contact-list">
    <li>
      <svg viewBox="0 0 24 22" aria-hidden="true">
        <path fill="#2b73b9" d="M2 8c0-3 4-5 10-5s10 2 10 5v2h-5V8c-2-1-8-1-10 0v2H2z"/>
        <rect x="5" y="11" width="14" height="9" rx="2" fill="#2b73b9"/>
        <circle cx="12" cy="15.5" r="2.5" fill="#f7f7f7"/>
      </svg>
      <span>123 456 7890</span>
    </li>
    <li>
      <svg viewBox="0 0 24 22" aria-hidden="true">
        <rect x="1" y="4" width="22" height="15" fill="#2b73b9"/>
        <path d="M2 5l10 8 10-8" fill="none" stroke="#f7f7f7" stroke-width="1.6"/>
        <path d="M2 18l7-6M22 18l-7-6" stroke="#f7f7f7" stroke-width="1.2"/>
      </svg>
      <span>omar@sbpbuilding.com.au</span>
    </li>
    <li>
      <svg viewBox="0 0 24 22" aria-hidden="true">
        <rect x="2" y="1" width="20" height="20" rx="3" fill="#2b73b9"/>
      </svg>
      <span>sbp_building</span>
    </li>
  </ul>

  <div class="service-rule"></div>
  <p class="services">Home Improvement Projects<span class="sep">|</span>House Extensions<span class="sep">|</span>House Renovations</p>
</section>

<section class="card card--back" aria-label="Business card back">
  <div class="wordmark">
    <span class="wordmark__sub">Stonebridge</span>
    <span class="wordmark__sub">Building and Projects</span>
  </div>

  <div class="service-rule"></div>
  <p class="services">Bathroom and Kitchen Renovations<span class="sep">|</span>New Builds and Granny Flats</p>
</section>

</body>
</html>
```